Captivating packaging design for sports company.

We need a packaging design that encompasses our resistance bands workout set. Our focus is quality, convenience, and versatility. The design should be tailored to our broad array of customer across all paths. We would like the packaging to reflect our brand and product features such as: the LBS(weight) listed on each of the bands, convenience for travel and at home, highest quality, for all fitness levels, and free eBook. We'd also like to include a couple of our reviews on the packaging. Please refer to our listing on Varlo for additional information https://www.shopvarlo.com/Brisklane-Athletics-Resistance-Workout-Carrying/dp/K47TR2XMNQ/ref=sr_1_1?ie=UTF8&qid=1470453588&sr=8-1&keywords=brisklane+athletics+resistance+bands
Please reach out with additional questions for any further details. Thank you.
Target Market(s)
Sports, fitness, and health enthusiasts of all ages.
Industry/Entity Type
It Company
Look and feel
Each slider illustrates characteristics of the customer's brand and the style your logo design should communicate.

```html
<!DOCTYPE html>
<html lang="en">
<head>
<meta charset="utf-8">
<title>Brisklane Athletics – Resistance Band Packaging</title>
<link rel="stylesheet" href="https://fonts.googleapis.com/css2?family=Questrial&display=swap">
<style>
  :root {
    --page-bg: #ececec;
    --face-top: #f6f6f6;
    --face-bottom: #e1e1e1;
    --maroon: #6e1a1f;
    --maroon-deep: #5a1418;
    --charcoal: #2c2c2c;
    --title-ink: #ffffff;
    --sub-ink: #cfcfcf;
    --photo-light: #cfcfcf;
    --photo-dark: #3a3a3a;
  }
  html, body {
    margin: 0;
    width: 1200px;
    height: 900px;
    overflow: hidden;
    background: var(--page-bg);
    font-family: "Questrial", "Century Gothic", sans-serif;
  }
  .canvas {
    position: relative;
    width: 1200px;
    height: 900px;
  }
  .package-front {
    position: absolute;
    left: 280px;
    top: 95px;
    width: 640px;
    height: 710px;
    background: linear-gradient(180deg, var(--face-top), var(--face-bottom));
    overflow: hidden;
  }
  .package-shapes {
    position: absolute;
    inset: 0;
  }
  .brand {
    position: absolute;
    left: 36px;
    top: 92px;
    display: flex;
    align-items: center;
    gap: 14px;
    color: var(--maroon);
  }
  .brand-dot {
    width: 52px;
    height: 52px;
    border-radius: 50%;
    background: var(--maroon);
  }
  .brand-name {
    font-size: 29px;
    line-height: 1.05;
    letter-spacing: 0.04em;
    text-transform: uppercase;
  }
  .product-title {
    position: absolute;
    left: 334px;
    top: 70px;
    margin: 0;
    font-weight: 400;
    font-size: 35px;
    line-height: 1.3;
    color: var(--title-ink);
  }
  .product-subtitle {
    position: absolute;
    left: 336px;
    top: 182px;
    margin: 0;
    font-size: 19px;
    line-height: 1.6;
    font-style: italic;
    color: var(--sub-ink);
  }
  .athlete-photo {
    position: absolute;
    left: 76px;
    top: 262px;
    width: 222px;
    height: 336px;
    background: radial-gradient(ellipse at 55% 45%, var(--photo-dark) 0%, #6a6a6a 45%, var(--photo-light) 80%);
    opacity: 0.85;
  }
</style>
</head>
<body>
<main class="canvas">
  <section class="package-front">
    <svg class="package-shapes" width="640" height="710" viewBox="0 0 640 710" aria-hidden="true">
      <rect class="edge-strip" x="0" y="0" width="12" height="330" fill="var(--maroon)"/>
      <polygon class="title-panel" points="319,48 550,48 324,416 319,416" fill="var(--charcoal)"/>
      <polygon class="corner-wedge" points="640,38 640,710 209,710" fill="var(--maroon)"/>
      <polygon class="corner-wedge-shade" points="640,300 640,710 420,710" fill="var(--maroon-deep)" opacity="0.5"/>
    </svg>

    <div class="brand">
      <span class="brand-dot"></span>
      <span class="brand-name">Brisklane<br>Athletics</span>
    </div>

    <h1 class="product-title">Resistance<br>Band</h1>
    <p class="product-subtitle">Workout Set<br>with<br>Door<br>Anchor</p>

    <div class="athlete-photo" role="img" aria-label="Black and white photo of a woman in a lunge pulling a resistance band"></div>
  </section>
</main>
</body>
</html>
```